Logo with Stationery Design Project-

The company is an on-line service for assisting the people that are in a foreclosure situation with their homes. We are presently building the site on WebMarlin with Wordpress.

The best option to save a home in the USA at the end of the line with the banks is to file for bankruptcy Chapter 7 or Chapter 13. We work with homeowners and attorneys to prepare the financial package for the attorneys to negotiate with the banks after filing for bankruptcy. We also sell a binder on-line which is called the northgate renewal set and the web site is: www.northgaterenewalset.example
We need a logo and stationnary to communicate the message of advisors in the field of financial strategies when it comes to the foreclosure and bankruptcy process. This stationnary will be printed on high quality paper with the business cards being on 100 stock which is high quality in the USA.

We would like to see the logo to use the Navy blue and Aqua Green colors. The final desing should communicate the financial knowledge and promise of a light at the end of the tunnell.

The card should use both sides with the back side being the logo and the web site address that links with the front of the card. Letterhead and envelopes should be serious but sexy!

A challenge that I am sure someone is up to........

Target Market(s)

12 million people that are in foreclosure in the USA and all of the law firms that deal with foreclosure and bankruptcies in the USA all 50 states

Industry/Entity Type

Financial

Requirements
Must have
• Colors are important = Navy blue and Aqua green

```html
<!DOCTYPE html>
<html lang="en">
<head>
<meta charset="utf-8">
<title>Northgate Renewal Set – Stationery</title>
<link rel="stylesheet" href="https://fonts.googleapis.com/css2?family=Source+Sans+3:wght@400;600&display=swap">
<style>
  :root {
    --backdrop: #c3b49a;
    --teal: #2c9995;
    --teal-light: #4fb5b0;
    --teal-deep: #1d7f7d;
    --navy: #17305a;
    --navy-dark: #102447;
    --paper: #ffffff;
    --ink: #2b2b2b;
    --house-tint: #e4f1f1;
  }
  * { box-sizing: border-box; margin: 0; padding: 0; }
  html, body { width: 1200px; height: 848px; overflow: hidden; }
  body {
    background: var(--backdrop);
    font-family: "Source Sans 3", "Myriad Pro", sans-serif;
    position: relative;
  }
  .piece { position: absolute; }

  /* ---------- business card back ---------- */
  .card-back {
    width: 37.8em; height: 22.1em;
    background: radial-gradient(ellipse at 50% 35%, var(--teal-light) 0%, var(--teal) 55%, var(--teal-deep) 100%);
    overflow: hidden;
  }
  .card-back .brand {
    position: absolute; left: 0; right: 0; top: 9em;
    text-align: center; color: var(--navy);
  }
  .card-back .brand-name {
    font-size: 1.9em; font-weight: 600; line-height: 1.2; letter-spacing: 0.02em;
    white-space: nowrap;
  }
  .card-back .brand-url {
    margin-top: 0.4em;
    font-size: 1.25em; font-weight: 600; line-height: 1.2; white-space: nowrap;
  }
  .card-back .band-navy {
    position: absolute; left: 0; right: 0; top: 17.9em; height: 2.2em;
    background: var(--navy);
  }

  /* ---------- business card front ---------- */
  .card-front {
    width: 37.8em; height: 21.8em;
    background: var(--paper); overflow: hidden;
  }
  .card-front .houses {
    position: absolute; left: 1.4em; top: 8.6em; width: 13.6em; height: 8.8em;
    background: linear-gradient(180deg, var(--paper), var(--house-tint));
  }
  .card-front .info {
    position: absolute; left: 18.2em; top: 4.4em;
    color: var(--navy); white-space: nowrap;
  }
  .card-front .person { font-size: 1.7em; line-height: 1.2; }
  .card-front .role { font-size: 1.1em; line-height: 1.2; }
  .card-front .contacts {
    list-style: none; margin: 1.4em 0 0 1em;
    font-size: 0.85em; line-height: 1.6em;
  }
  .card-front .contacts li { display: flex; align-items: center; gap: 0.7em; }
  .card-front .contacts svg { width: 0.9em; height: 0.9em; fill: var(--navy); flex: none; }
  .card-front .band-teal {
    position: absolute; left: 0; right: 0; top: 17.8em; height: 1.8em;
    background: var(--teal);
  }

  /* ---------- letterhead ---------- */
  .letterhead {
    width: 40.4em; height: 57.3em;
    background: var(--paper); overflow: hidden;
    box-shadow: 0 0 0 0.05em rgba(0,0,0,0.05);
  }
  .letterhead .houses {
    position: absolute; left: 1em; top: 0.6em; width: 9em; height: 3.6em;
    background: linear-gradient(180deg, var(--paper), var(--house-tint));
  }
  .letterhead .slogan {
    position: absolute; right: 1.4em; top: 1.9em;
    color: var(--navy); font-size: 1.2em; line-height: 1.2;
  }
  .letterhead .band-teal {
    position: absolute; left: 0; right: 0; top: 4.4em; height: 1em;
    background: var(--teal);
  }
  .letterhead .date {
    position: absolute; right: 2.8em; top: 8.6em;
    color: var(--ink); font-size: 0.85em;
  }
  .letterhead .salutation {
    position: absolute; left: 3.3em; top: 19em;
    color: var(--ink); font-size: 0.9em;
  }
  .letterhead .body-text {
    position: absolute; left: 3.3em; top: 22.2em; width: 37em;
    color: var(--ink); font-size: 0.9em; line-height: 1.3em;
  }
  .letterhead .footer-url {
    position: absolute; right: 2em; bottom: 2.4em;
    color: var(--navy); font-size: 0.7em;
  }

  /* ---------- envelope ---------- */
  .envelope {
    width: 43.6em; height: 30.2em;
    background: var(--teal);
    border-radius: 3em 3em 0 0; overflow: hidden;
  }
  .envelope .body {
    position: absolute; left: 0; right: 0; top: 2.6em; bottom: 0;
    background: radial-gradient(ellipse at 30% 40%, #1f4270 0%, var(--navy) 55%, var(--navy-dark) 100%);
    border-radius: 3em 3em 0 0;
  }
  .envelope .address-line {
    position: absolute; left: 21.7em; width: 19.2em; height: 0.1em;
    background: var(--teal-light);
  }
  .envelope .brand {
    position: absolute; left: 1.1em; top: 22.3em;
    color: var(--teal-light); white-space: nowrap;
  }
  .envelope .brand-name { font-size: 1.1em; font-weight: 600; line-height: 1.2; }
  .envelope .brand-url { margin-top: 0.2em; font-size: 0.8em; line-height: 1.2; }
  .envelope .band-teal {
    position: absolute; left: 0; right: 0; top: 26.3em; height: 1.5em;
    background: var(--teal);
  }
</style>
</head>
<body>

  <!-- card back, top left -->
  <div class="piece card-back" style="left:3px; top:3px; font-size:10px;">
    <div class="brand">
      <div class="brand-name">Northgate Renewal Set</div>
      <div class="brand-url">www.northgaterenewalset.example</div>
    </div>
    <div class="band-navy"></div>
  </div>

  <!-- card front -->
  <div class="piece card-front" style="left:3px; top:254px; font-size:10px;">
    <div class="houses" role="img" aria-label="Outline drawing of a row of houses"></div>
    <div class="info">
      <div class="person">Name Surname</div>
      <div class="role">on-line service</div>
      <ul class="contacts">
        <li><svg viewBox="0 0 10 10"><path d="M2 0.5h2l0.6 2.4-1.2 0.8a6 6 0 0 0 2.9 2.9l0.8-1.2 2.4 0.6v2a1 1 0 0 1-1 1A8.5 8.5 0 0 1 1 1.5a1 1 0 0 1 1-1z"/></svg>123 / 456-789</li>
        <li><svg viewBox="0 0 10 10"><path d="M5 4.2 9 1.5v2.2L6.2 5.4 9 7.1v2.2L5 6.6 1 9.3V7.1l2.8-1.7L1 3.7V1.5z"/></svg>www.northgaterenewalset.example</li>
        <li><svg viewBox="0 0 10 10"><circle cx="5" cy="5" r="4.5"/></svg>name@mailbox.example</li>
      </ul>
    </div>
    <div class="band-teal"></div>
  </div>

  <!-- letterhead, tilted -->
  <div class="piece letterhead" style="left:470px; top:150px; font-size:10px; transform:rotate(-20deg);">
    <div class="houses" role="img" aria-label="Outline drawing of a row of houses"></div>
    <div class="slogan">Save your home with us!</div>
    <div class="band-teal"></div>
    <div class="date">City, 24.10.2011.</div>
    <div class="salutation">Dear,</div>
    <p class="body-text">Lorem Ipsum is simply dummy text of the printing and typesetting industry. Lorem Ipsum has been the industry's standard dummy text ever since the 1500s, when an unknown printer took a galley of type and scrambled it to make a type specimen book. It has survived not only five centuries, but also the leap into electronic typesetting, remaining essentially unchanged. It was popularised in the 1960s with the release of Letraset sheets containing Lorem Ipsum passages, and more recently with desktop publishing software like Aldus PageMaker including versions of Lorem Ipsum.</p>
    <div class="footer-url">www.northgaterenewalset.example</div>
  </div>

  <!-- letterhead, straight -->
  <div class="piece letterhead" style="left:770px; top:103px; font-size:10.2px;">
    <div class="houses" role="img" aria-label="Outline drawing of a row of houses"></div>
    <div class="slogan">Save your home with us!</div>
    <div class="band-teal"></div>
    <div class="date">City, 24.10.2011.</div>
    <div class="salutation">Dear,</div>
    <p class="body-text">Lorem Ipsum is simply dummy text of the printing and typesetting industry. Lorem Ipsum has been the industry's standard dummy text ever since the 1500s, when an unknown printer took a galley of type and scrambled it to make a type specimen book. It has survived not only five centuries, but also the leap into electronic typesetting, remaining essentially unchanged. It was popularised in the 1960s with the release of Letraset sheets containing Lorem Ipsum passages, and more recently with desktop publishing software like Aldus PageMaker including versions of Lorem Ipsum.</p>
    <div class="footer-url">www.northgaterenewalset.example</div>
  </div>

  <!-- envelope -->
  <div class="piece envelope" style="left:752px; top:442px; font-size:10px;">
    <div class="body"></div>
    <div class="address-line" style="top:17.1em;"></div>
    <div class="address-line" style="top:19.9em;"></div>
    <div class="address-line" style="top:22.5em;"></div>
    <div class="brand">
      <div class="brand-name">Northgate Renewal Set</div>
      <div class="brand-url">www.northgaterenewalset.example</div>
    </div>
    <div class="band-teal"></div>
  </div>

  <!-- stack of card backs -->
  <div class="piece card-back" style="left:249px; top:534px; font-size:7.55px;">
    <div class="band-navy"></div>
  </div>
  <div class="piece card-back" style="left:270px; top:559px; font-size:7.55px; box-shadow:-2px -2px 4px rgba(0,0,0,0.15);">
    <div class="band-navy"></div>
  </div>
  <div class="piece card-back" style="left:296px; top:584px; font-size:7.55px; box-shadow:-2px -2px 4px rgba(0,0,0,0.15);">
    <div class="brand">
      <div class="brand-name">Northgate Renewal Set</div>
      <div class="brand-url">www.northgaterenewalset.example</div>
    </div>
    <div class="band-navy"></div>
  </div>

  <!-- stack of card fronts -->
  <div class="piece card-front" style="left:30px; top:650px; font-size:7.7px; transform:rotate(-4deg); box-shadow:0 0 3px rgba(0,0,0,0.15);">
    <div class="band-teal"></div>
  </div>
  <div class="piece card-front" style="left:36px; top:636px; font-size:7.7px; transform:rotate(-8deg); box-shadow:0 0 3px rgba(0,0,0,0.15);">
    <div class="band-teal"></div>
  </div>
  <div class="piece card-front" style="left:44px; top:624px; font-size:7.7px; transform:rotate(-12deg); box-shadow:0 0 3px rgba(0,0,0,0.2);">
    <div class="houses" role="img" aria-label="Outline drawing of a row of houses"></div>
    <div class="info">
      <div class="person">Name Surname</div>
      <div class="role">on-line service</div>
      <ul class="contacts">
        <li><svg viewBox="0 0 10 10"><path d="M2 0.5h2l0.6 2.4-1.2 0.8a6 6 0 0 0 2.9 2.9l0.8-1.2 2.4 0.6v2a1 1 0 0 1-1 1A8.5 8.5 0 0 1 1 1.5a1 1 0 0 1 1-1z"/></svg>123 / 456-789</li>
        <li><svg viewBox="0 0 10 10"><path d="M5 4.2 9 1.5v2.2L6.2 5.4 9 7.1v2.2L5 6.6 1 9.3V7.1l2.8-1.7L1 3.7V1.5z"/></svg>www.northgaterenewalset.example</li>
        <li><svg viewBox="0 0 10 10"><circle cx="5" cy="5" r="4.5"/></svg>name@mailbox.example</li>
      </ul>
    </div>
    <div class="band-teal"></div>
  </div>

</body>
</html>
```